Brimline sales

🎨 Project Title:
Brimline Designer Web Page for WooCommerce (French Texts Provided) i show you exemple what i need

📄 Project Description:
We are looking to create a web page design (desktop and mobile) for a custom cap ordering experience. This page will be integrated into our existing WooCommerce transactional site. The goal is to allow customers to configure and order personalized caps easily and visually.

The entire interface will ultimately be in French, but you can design using placeholder texts (we will provide the actual French text later).

💡 Page Goals & Features:
The page should be modern, clean, and conversion-oriented, and include the following features:

Header area:

Visually showcase examples of designed caps (carousel or grid layout)

A clear title and short description

Customization Steps (in order):

Material selection: users choose the type of material for the cap

Cap color: users choose the base color of the cap

Patch shape: users select the shape of the patch (e.g., round, square, rectangle, custom)

Patch location: mainly the front, but possibly add other options

Quantity selection: users choose how many units they want (with price updates)

Price display: show price per unit and total cost depending on quantity

Call to Action (CTA):

Add to cart or request a quote button

Smooth integration with WooCommerce logic (cart, checkout, etc.)

Other Optional Sections:

FAQ

Delivery timeline

Client testimonials or reviews

🛠 Technical Notes:
The design must be compatible with WooCommerce

Responsive design for both desktop and mobile

The final output can be delivered in Figma, Adobe XD, or layered PSD (no coding required for now)

We will handle the French translation; just use placeholder text where needed

🖼 Inspiration / Style:
Clean and modern layout

Easy to navigate

Visual configurator-style approach (like t-shirt or shoe customization sites)

Feel free to use mockups of caps to enhance the presentation

📎 What we will provide:
Actual French text

Product images (caps, patch styles, color swatches)

Brand logo and colors

Optional references if needed

✅ Deliverables:
Homepage (or dedicated product page) layout

Mobile and desktop views

Editable design file (Figma, XD, PSD)

i need very nice 1 or 2 hat design to present to customer design un der the hat and front and see coupple of shape of the patche to show option possible

```html
<!DOCTYPE html>
<html lang="en">
<head>
<meta charset="utf-8">
<title>Brimline – Custom Straw Hats</title>
<link href="https://fonts.googleapis.com/css2?family=Montserrat:wght@400;500;600;700&display=swap" rel="stylesheet">
<style>
:root{
  --teal:#3aa39b;
  --teal-dark:#2e8a83;
  --coral:#e57373;
  --ink:#222;
  --muted:#555;
  --dark:#1d1e1f;
  --white:#fff;
}
*{box-sizing:border-box;margin:0;padding:0}
html,body{width:1200px;height:4107px;overflow:hidden}
body{font-family:"Montserrat",sans-serif;color:var(--ink);background:linear-gradient(#eefaf8 0,#fff 500px);position:relative}
.abs{position:absolute}
.nav{left:51px;top:45px;width:1095px;height:87px;border-radius:44px;background:var(--teal);color:#fff;display:flex;align-items:center;padding:0 62px}
.brand{font-size:32px;font-weight:500;width:310px}
.nav ul{list-style:none;display:flex;gap:42px;font-size:16px}
.nav li.active{font-weight:700}
.nav .icons{margin-left:auto;display:flex;gap:22px}
.hero{left:60px;top:207px;width:1085px;height:568px;border-radius:28px;overflow:hidden}
.hero-photo{position:absolute;inset:0;background:linear-gradient(180deg,#8cc6e8 0%,#bfe3ef 35%,#e4d6bd 62%,#b48e6f 100%)}
.hero-fade{position:absolute;inset:0;background:linear-gradient(90deg,rgba(255,255,255,.95) 0%,rgba(255,255,255,.78) 38%,rgba(255,255,255,0) 62%)}
.hero h1{position:absolute;left:52px;top:100px;font-size:49px;font-weight:500;line-height:62px;color:var(--teal)}
.hero h1 span{color:var(--coral)}
.hero p{position:absolute;left:52px;top:250px;font-size:24px;line-height:40px;color:#333;width:480px}
.btn{display:flex;align-items:center;justify-content:center;color:#fff;background:var(--teal);border-radius:5px;font-size:17px}
.section-title{left:0;width:1200px;text-align:center;font-size:35px;font-weight:500}
.section-title b{font-weight:700;color:var(--teal)}
.rule{height:3px;background:var(--ink)}
.photo{background:linear-gradient(180deg,#e9e7e3 0%,#f3f0ea 50%,#c69a6b 80%,#a7794b 100%);border-radius:18px}
.thumb{border:1px solid var(--teal);border-radius:10px;background:linear-gradient(135deg,#d2b07a,#e9c85a)}
.t-title{font-size:24px;font-weight:500}
.label{font-size:18px;font-weight:500;color:#333}
.small{font-size:12px;color:#555}
.mat{width:67px;height:48px;border-radius:5px}
.dot{width:30px;height:30px;border-radius:50%}
.box{border:1.5px solid var(--teal);border-radius:5px;display:flex;align-items:center;justify-content:space-around;font-size:20px}
.timeline{left:65px;top:1720px;width:1076px;height:386px;background:var(--teal);border-radius:16px;color:#fff}
.step{position:absolute;width:180px;text-align:center;font-size:21px;line-height:28px}
.step .ic{width:66px;height:66px;border-radius:50%;background:#fff;margin:0 auto 12px;display:flex;align-items:center;justify-content:center}
.arrow{position:absolute;top:190px}
.reviews{left:0;top:2200px;width:1200px;height:790px;background:linear-gradient(180deg,#4b5656,#3a4646 60%,#566060)}
.card{position:absolute;top:236px;width:327px;height:244px;background:#fff;border-radius:10px;padding:28px 32px;font-size:16px;line-height:29px;color:#444}
.card .q{font-size:40px;font-weight:700;color:var(--teal);line-height:30px}
.card .stars{position:absolute;right:32px;top:32px;color:var(--teal);font-size:22px;letter-spacing:2px}
.pill{position:absolute;top:516px;height:53px;border-radius:27px;background:#fff;display:flex;align-items:center;font-size:19px;padding-left:6px;gap:10px;color:#333}
.pill.on{background:var(--teal);color:#fff}
.avatar{width:44px;height:44px;border-radius:50%;background:linear-gradient(#c9a88c,#8a6a55)}
.faq{border:2px solid var(--teal);border-radius:8px;font-size:19px;color:#333;display:flex;align-items:center;justify-content:space-between;padding:0 32px}
.faq.open{background:var(--teal);color:#fff;display:block;padding:26px 32px}
.footer{left:0;top:3660px;width:1200px;height:447px;background:var(--dark);color:#fff;text-align:center}
.footer ul{list-style:none;display:flex;justify-content:center;gap:66px;font-size:16px}
.social{width:34px;height:34px;border-radius:50%;background:#fff;display:inline-block;margin:0 7px}
</style>
</head>
<body>

<header class="nav abs">
  <div class="brand">Brimline</div>
  <ul><li class="active">Home</li><li>Customize</li><li>FAQ</li><li>Contact</li><li>Testimonials</li></ul>
  <div class="icons">
    <svg width="26" height="28" viewBox="0 0 26 28" fill="none" stroke="#fff" stroke-width="2"><rect x="3" y="9" width="20" height="17" rx="2"/><path d="M8 9V6a5 5 0 0110 0v3"/></svg>
    <svg width="26" height="28" viewBox="0 0 26 28" fill="none" stroke="#fff" stroke-width="2"><circle cx="13" cy="8" r="6"/><path d="M2 27c1-7 6-10 11-10s10 3 11 10"/></svg>
  </div>
</header>

<section class="hero abs">
  <div class="hero-photo" role="img" aria-label="Straw hats with bright custom patches on a wooden beach deck by the sea"></div>
  <div class="hero-fade"></div>
  <h1>Design Your <span>Custom</span><br>Straw Hat</h1>
  <p>Select your material, color, and patch style — order directly online.</p>
  <div class="btn abs" style="left:52px;top:364px;width:185px;height:51px">Customize Now</div>
</section>

<h2 class="section-title abs" style="top:872px">Custom Order <b>Configuration</b></h2>
<div class="rule abs" style="left:502px;top:938px;width:190px"></div>

<div class="photo abs" style="left:113px;top:1004px;width:450px;height:440px" role="img" aria-label="Straw hat with front patch and underside view on a wooden shelf"></div>
<div class="thumb abs" style="left:112px;top:1474px;width:140px;height:115px" role="img" aria-label="Hat front view"></div>
<div class="thumb abs" style="left:268px;top:1474px;width:140px;height:115px" role="img" aria-label="Hat underside patch view"></div>
<div class="thumb abs" style="left:421px;top:1474px;width:142px;height:115px" role="img" aria-label="Hat side view"></div>

<div class="t-title abs" style="left:599px;top:1002px">The Wave Cap – Fully Customizable</div>
<div class="abs" style="left:599px;top:1044px;font-size:24px;font-weight:600">$ 119.99</div>
<div class="label abs" style="left:599px;top:1092px">Choose Your Material</div>
<div class="mat abs" style="left:599px;top:1130px;background:linear-gradient(135deg,#b8764e,#e2b48a)" role="img" aria-label="Rush grass texture"></div>
<div class="mat abs" style="left:687px;top:1130px;background:linear-gradient(135deg,#c5a273,#8f6a3e)" role="img" aria-label="Mat grass texture"></div>
<div class="mat abs" style="left:776px;top:1130px;background:linear-gradient(135deg,#c98559,#9a5c3b)" role="img" aria-label="Hollow grass texture"></div>
<div class="mat abs" style="left:864px;top:1130px;background:linear-gradient(135deg,#f1d89a,#d9bb78)" role="img" aria-label="Rush and mat grass texture"></div>
<div class="small abs" style="left:599px;top:1190px">Rush Grass</div>
<div class="small abs" style="left:687px;top:1190px">Mat Grass</div>
<div class="small abs" style="left:776px;top:1190px">Hollow Grass</div>
<div class="small abs" style="left:864px;top:1190px">Rush + Mat Grass</div>
<div class="dot abs" style="left:602px;top:1230px;background:#c9c3b6;border:2px solid #e4e0d8"></div>
<div class="dot abs" style="left:653px;top:1230px;background:#2c9ad1"></div>
<div class="dot abs" style="left:704px;top:1230px;background:#4d4d4d"></div>
<div class="dot abs" style="left:755px;top:1230px;background:#d8a3a3"></div>

<div class="label abs" style="left:599px;top:1282px">Select Shape</div>
<div class="label abs" style="left:791px;top:1282px">Patch Position</div>
<div class="abs" style="left:599px;top:1323px;width:35px;height:35px;background:var(--teal)"></div>
<div class="abs" style="left:652px;top:1323px;width:35px;height:35px;border-radius:50%;background:var(--teal)"></div>
<div class="abs" style="left:700px;top:1326px;width:52px;height:29px;background:var(--teal)"></div>
<div class="abs" style="left:599px;top:1375px;font-size:15px;color:#444;display:flex;align-items:center;gap:6px">
  <svg width="18" height="18" viewBox="0 0 18 18" fill="none" stroke="#444" stroke-width="1.5"><circle cx="9" cy="9" r="7.5"/><path d="M5 9l3 3 5-6"/></svg>Custom Shape</div>
<div class="thumb abs" style="left:791px;top:1317px;width:70px;height:51px;background:linear-gradient(#fff,#d6b57c)" role="img" aria-label="Patch on front of hat"></div>
<div class="thumb abs" style="left:877px;top:1317px;width:71px;height:51px;background:linear-gradient(#fff,#d6b57c)" role="img" aria-label="Patch on back of hat"></div>
<div class="small abs" style="left:795px;top:1378px">Front</div>
<div class="small abs" style="left:880px;top:1378px">Back</div>

<div class="label abs" style="left:599px;top:1422px">Quantity</div>
<div class="label abs" style="left:776px;top:1422px">Total Price</div>
<div class="box abs" style="left:599px;top:1462px;width:141px;height:40px"><span>−</span><span>5</span><span>+</span></div>
<div class="box abs" style="left:776px;top:1462px;width:158px;height:40px;justify-content:center;font-weight:600">$ 600</div>
<div class="btn abs" style="left:599px;top:1540px;width:181px;height:49px">Add to Cart</div>
<div class="btn abs" style="left:794px;top:1540px;width:206px;height:49px;background:var(--coral)">Request a Quote</div>

<section class="timeline abs">
  <h2 class="section-title abs" style="top:58px;width:1076px;color:#fff">Total <b style="color:#fff">Estimated Time</b></h2>
  <div class="rule abs" style="left:429px;top:120px;width:207px;background:#fff"></div>
  <div class="step" style="left:39px;top:170px"><div class="ic"><svg width="36" height="26" viewBox="0 0 36 26" fill="none" stroke="#333" stroke-width="1.8"><path d="M9 18c0-10 4-15 9-15s9 5 9 15"/><ellipse cx="18" cy="19" rx="16" ry="5"/></svg></div>Customization<br>Submitted</div>
  <div class="step" style="left:248px;top:170px"><div class="ic"><svg width="32" height="32" viewBox="0 0 32 32" fill="none" stroke="#333" stroke-width="1.8"><path d="M6 13l10-5 10 5v12l-10 5-10-5z"/><path d="M6 13l10 5 10-5M16 18v12"/></svg></div>Production<br>Begins</div>
  <div class="step" style="left:457px;top:170px"><div class="ic"><svg width="30" height="32" viewBox="0 0 30 32" fill="none" stroke="#333" stroke-width="1.8"><rect x="5" y="3" width="16" height="24" rx="2"/><circle cx="21" cy="23" r="5"/><path d="M9 10h8M9 15h6"/></svg></div>Patching &amp;<br>Assembly</div>
  <div class="step" style="left:666px;top:170px"><div class="ic"><svg width="32" height="32" viewBox="0 0 32 32" fill="none" stroke="#333" stroke-width="1.8"><circle cx="16" cy="19" r="9"/><path d="M12 19l3 3 5-6M8 6l2 3M16 3v4M24 6l-2 3"/></svg></div>Quality Check &amp;<br>Packaging</div>
  <div class="step" style="left:876px;top:170px"><div class="ic"><svg width="36" height="28" viewBox="0 0 36 28" fill="none" stroke="#333" stroke-width="1.8"><rect x="3" y="5" width="19" height="14"/><path d="M22 10h6l5 5v4H22"/><circle cx="10" cy="21" r="3"/><circle cx="27" cy="21" r="3"/></svg></div>Shipped to<br>You</div>
  <svg class="arrow" style="left:180px" width="110" height="30" viewBox="0 0 110 30" fill="none" stroke="#fff" stroke-width="2"><path d="M4 10q50 30 100 0M96 4l8 6-10 4"/></svg>
  <svg class="arrow" style="left:388px" width="110" height="30" viewBox="0 0 110 30" fill="none" stroke="#fff" stroke-width="2"><path d="M4 10q50 30 100 0M96 4l8 6-10 4"/></svg>
  <svg class="arrow" style="left:603px" width="110" height="30" viewBox="0 0 110 30" fill="none" stroke="#fff" stroke-width="2"><path d="M4 10q50 30 100 0M96 4l8 6-10 4"/></svg>
  <svg class="arrow" style="left:810px" width="110" height="30" viewBox="0 0 110 30" fill="none" stroke="#fff" stroke-width="2"><path d="M4 10q50 30 100 0M96 4l8 6-10 4"/></svg>
</section>

<section class="reviews abs" role="img" aria-label="Woman in a straw hat on a rocky beach, darkened backdrop">
  <svg class="abs" style="left:0;top:0" width="1200" height="40" viewBox="0 0 1200 40"><path d="M0 0H1200V0Q600 50 0 0Z" fill="#fff"/></svg>
  <h2 class="section-title abs" style="top:108px;color:#fff">What Our <b style="color:#fff">Customers Are Saying</b></h2>
  <div class="rule abs" style="left:526px;top:170px;width:140px;background:#fff"></div>
  <div class="card" style="left:80px"><div class="q">”</div><div class="stars">★★★★★</div><p style="margin-top:12px">The caps turned out amazing! Super high quality, and the customization process was so smooth. Will definitely order again.</p></div>
  <div class="card" style="left:440px"><div class="q">”</div><div class="stars">★★★★★</div><p style="margin-top:12px">I ordered 25 caps for my shop. The material feels premium, and the logo placement was perfect. The team even helped adjust my file.</p></div>
  <div class="card" style="left:800px"><div class="q">”</div><div class="stars">★★★★★</div><p style="margin-top:12px">Customizing the cap was actually fun. I could see my design live before ordering. It came out just like the preview.</p></div>
  <div class="pill on" style="left:80px;width:291px"><div class="avatar" role="img" aria-label="Customer photo"></div>— Noah T., Oregon</div>
  <div class="pill" style="left:440px;width:321px"><div class="avatar" role="img" aria-label="Customer photo"></div>— Claire D., Lyon</div>
  <div class="pill" style="left:800px;width:260px"><div class="avatar" role="img" aria-label="Customer photo"></div>— Arjun S., Kerala</div>
  <div class="abs" style="left:555px;top:644px;width:16px;height:16px;border-radius:50%;background:#9fd9cf"></div>
  <div class="abs" style="left:578px;top:644px;width:16px;height:16px;border-radius:50%;background:#9fd9cf"></div>
  <div class="abs" style="left:601px;top:640px;width:24px;height:24px;border-radius:50%;background:#fff"></div>
  <svg class="abs" style="left:0;top:740px" width="1200" height="50" viewBox="0 0 1200 50"><path d="M0 50Q600 -20 1200 30V50Z" fill="#fff"/></svg>
</section>

<h2 class="section-title abs" style="top:3042px">Frequently <b>Asked Questions</b></h2>
<div class="abs" style="left:0;top:3120px;width:1200px;height:1px;background:#e8e8e8"></div>

<div class="faq open abs" style="left:54px;top:3164px;width:531px;height:166px">
  <div style="display:flex;justify-content:space-between;font-weight:600">1. How do I customize my cap?<span>⌃</span></div>
  <p style="font-size:16px;line-height:26px;margin-top:14px">Use our step-by-step designer to choose the material, color, patch shape, and quantity. You'll see a live preview as you go.</p>
</div>
<div class="faq abs" style="left:615px;top:3164px;width:530px;height:67px">4. How long does delivery take?<span>⌄</span></div>
<div class="faq abs" style="left:615px;top:3263px;width:530px;height:67px">5. Do you ship internationally?<span>⌄</span></div>
<div class="faq abs" style="left:54px;top:3357px;width:531px;height:67px">2. Can I order just one custom cap?<span>⌄</span></div>
<div class="faq abs" style="left:615px;top:3357px;width:530px;height:67px">6. What if I'm not happy with my cap?<span>⌄</span></div>
<div class="faq abs" style="left:54px;top:3453px;width:531px;height:67px">3. Can I upload my own logo or design?<span>⌄</span></div>
<div class="faq abs" style="left:615px;top:3453px;width:530px;height:67px">7. Can I order just one cap?<span>⌄</span></div>
<div class="btn abs" style="left:504px;top:3575px;width:193px;height:50px">View All FAQs</div>

<footer class="footer abs">
  <svg class="abs" style="left:0;top:0" width="1200" height="70" viewBox="0 0 1200 70"><path d="M0 0H1200V0Q1150 50 700 60Q200 70 0 60Z" fill="#fff"/><path d="M0 60Q200 70 700 60Q1150 50 1200 10V22Q1150 62 700 72Q200 80 0 72Z" fill="var(--teal)"/></svg>
  <div style="position:absolute;top:118px;width:1200px;font-size:44px;font-weight:500">Brimline</div>
  <p style="position:absolute;top:192px;width:1200px;font-size:15px;line-height:23px">Brimline makes premium, personalized straw hats—<br>designed by you, handcrafted by us.</p>
  <ul style="position:absolute;top:272px;width:1200px"><li>HOME</li><li>CUSTOMIZE</li><li>FAQ</li><li>CONTACT</li><li>TESTIMONIALS</li></ul>
  <div style="position:absolute;top:326px;width:1200px"><span class="social"></span><span class="social"></span><span class="social"></span></div>
  <div style="position:absolute;top:398px;width:1200px;height:49px;background:var(--teal);font-size:13px;line-height:42px">© 2025 Brimline. All rights reserved.</div>
</footer>

</body>
</html>
```